Government Contracting business needs a website design.

Pellworth & Quine, LLC is a minority owned Service Disabled Veteran Owned Small Business (SDVOSB) that provides Strategic Planning, Public Health Emergency Response, and Data Management Solutions for Federal Civilian and Defense Agencies. We have over 20 years of experience helping health and defense agencies develop concept of operations, deploy assets and personnel in Hot Zones around the world, and deliver goods and services all of the globe.

We are a leader in the field of Data Management. We help our customers develop cloud migration and disaster recovery strategies. We are experts with database management, data replication, queries, consolidation, and records management.

We are looking for a very nice and simple website designs that states clearly what we do as a company and that is easy for our customers to follow. We would like to have some moving pictures that are base on our expertise. We want the website to be easy to use and have the scroll down features that keeps things all on the same page when clicking on the menu. I attached a document with what we need on the website. I will also attach our logo. We want it to look simple clean and very professional.

Target Market(s)

Government Contracting, Management Consulting, Health

Industry/Entity Type

Government

Coding

Coded - Design and coding required

Number of Pages Required

1 page

Font styles to use
Serif

Requirements
Must have
• Very nice picture slides that speaks to our capabilities in Disaster Response, Strategic Planning, and Database Management. Slick look and design. Make sure SDVOSB Logo is right at the beginning of website as our customers is looking for that certification. Very nice colors that blend well with our logo.
Nice to have
• Very nice and slick colors that blends well with logo.
Should not have
• Basic website design that are weary on the eye. No bright colors, just simple colors that looks good with logo.

```html
<!DOCTYPE html>
<html lang="en">
<head>
<meta charset="utf-8">
<title>Pellworth &amp; Quine, LLC</title>
<link rel="stylesheet" href="https://fonts.googleapis.com/css2?family=Open+Sans:wght@400;600;700&display=swap">
<style>
:root{
  --slate:#2c4a5d;
  --slate-deep:#1d3547;
  --orange:#f7941d;
  --ink:#333b42;
  --muted:#5a6168;
  --light:#ececec;
  --footer:#232323;
  --white:#ffffff;
}
*{box-sizing:border-box;margin:0;padding:0}
html,body{width:1200px;height:3455px;overflow:hidden}
body{position:relative;background:var(--white);font-family:"Open Sans",Arial,sans-serif;color:var(--ink)}
.abs{position:absolute}
.btn{position:absolute;display:flex;align-items:center;justify-content:center;background:var(--orange);color:var(--white);font-size:14px;font-weight:600;letter-spacing:.5px;text-transform:uppercase}
.section-title{position:absolute;left:0;width:1200px;text-align:center;font-size:28px;font-weight:400;letter-spacing:.5px;color:var(--ink)}

/* header */
.brand{position:absolute;display:flex;align-items:center;gap:14px}
.brand-mark{width:34px;height:34px;background:currentColor}
.brand-name{font-size:27px;font-weight:400;white-space:nowrap}
.header .brand{left:76px;top:60px;color:var(--slate)}
.cert-badge{position:absolute;left:996px;top:26px;width:128px;height:128px;border-radius:50%;background:#1c3f8f}

/* nav */
.nav{position:absolute;left:0;top:166px;width:1200px;height:56px;background:var(--slate)}
.nav a{position:absolute;top:19px;color:var(--white);font-size:13px;font-weight:600;text-decoration:none;letter-spacing:.3px}
.nav-phone{position:absolute;right:75px;top:14px;color:var(--white);font-size:21px;font-weight:600;display:flex;align-items:center;gap:14px}

/* hero */
.hero{position:absolute;left:0;top:222px;width:1200px;height:518px;background:linear-gradient(120deg,#3d4a44 0%,#6f7a76 30%,#cfd3d4 55%,#e9ebec 75%,#b8bec2 100%)}
.hero-caption{position:absolute;left:104px;top:146px;width:527px;height:160px;background:rgba(20,24,28,.88);padding:20px 0 0 0}
.hero-title{position:absolute;left:0;top:146px;padding-left:0}
.hero-caption h1{position:absolute;left:0;top:18px;font-size:41px;font-weight:700;color:var(--white);letter-spacing:.5px}
.hero-caption p{position:absolute;left:0;top:74px;width:500px;font-size:20px;line-height:26px;color:var(--white)}
.hero-dots{position:absolute;left:78px;top:398px;display:flex;gap:6px}
.hero-dots span{width:11px;height:11px;border-radius:50%;background:var(--white)}
.hero-dots span.active{background:var(--slate-deep)}

/* overview */
.overview-text{position:absolute;left:90px;top:838px;width:1020px;text-align:center;font-size:13.5px;line-height:29px;color:var(--muted)}

/* services */
.services{position:absolute;left:0;top:1085px;width:1200px;height:580px;background:linear-gradient(135deg,#1a3147 0%,#24405a 45%,#1b344a 100%)}
.services .section-title{color:var(--white);top:40px}
.service-card{position:absolute;background:var(--white);width:329px;height:355px;padding:0 24px}
.service-card svg{position:absolute;left:24px}
.service-card h3{position:absolute;left:24px;right:20px;font-size:16.5px;font-weight:700;color:var(--slate);line-height:22px;text-transform:uppercase}
.service-card ul{position:absolute;left:24px;list-style:none}
.service-card li{font-size:13px;line-height:30px;color:var(--ink);display:flex;align-items:center;gap:18px}
.service-card li::before{content:"";width:0;height:0;border-left:6px solid var(--slate-deep);border-top:4px solid transparent;border-bottom:4px solid transparent}

/* leadership */
.photo{position:absolute}
.name-tag{position:absolute;background:var(--slate);color:var(--white);padding:18px 0 0 22px}
.name-tag h4{font-size:19px;font-weight:700;line-height:22px;text-transform:uppercase}
.name-tag span{display:block;font-size:13.5px;font-weight:600;margin-top:4px;line-height:19px}
.bio{position:absolute;font-size:13.5px;line-height:25.5px;color:var(--muted)}

/* why hire */
.why{position:absolute;left:0;top:2568px;width:690px;height:364px;background:var(--light)}
.why h2{position:absolute;left:76px;top:56px;font-size:28px;font-weight:400;color:var(--ink)}
.why ul{position:absolute;left:76px;top:112px;width:580px;list-style:none}
.why li{position:relative;padding-left:33px;font-size:13.5px;line-height:24px;color:var(--ink);margin-bottom:9px}
.why li svg{position:absolute;left:0;top:4px}
.why-brand{position:absolute;left:690px;top:2568px;width:510px;height:364px;background:var(--slate)}
.why-brand .brand{left:72px;top:156px;color:var(--white)}
.why-brand .brand-name{font-size:36px}
.why-brand .brand-mark{width:42px;height:42px}

/* partners */
.partner{position:absolute;top:3035px;width:242px;height:111px;border:1px solid #d6d6d6;display:flex;align-items:center;justify-content:center;font-size:22px;font-weight:700;color:var(--slate)}
.partner.boxed{border:3px solid var(--slate-deep)}

/* footer */
.footer{position:absolute;left:0;top:3201px;width:1200px;height:254px;background:var(--footer);color:#cfcfcf}
.footer .brand{left:76px;top:58px;color:var(--white);gap:10px}
.footer .brand-name{font-size:22px}
.footer .brand-mark{width:26px;height:26px}
.footer-copy{position:absolute;left:76px;top:118px;font-size:12px;line-height:24px;color:#9a9a9a}
.socials{position:absolute;left:76px;top:184px;display:flex;gap:18px}
.socials span{width:16px;height:16px;background:var(--white)}
.footer h5{position:absolute;top:44px;font-size:14px;font-weight:700;color:var(--white);letter-spacing:.4px}
.footer .rule{position:absolute;top:73px;height:1px;background:#4a4a4a}
.footer ul{position:absolute;top:88px;list-style:none}
.footer li{font-size:12.5px;line-height:28px;color:#cfcfcf;display:flex;align-items:center;gap:16px}
.page-mark{position:absolute;right:16px;top:3390px;font-size:13px;color:#8a8a8a}
</style>
</head>
<body>

<header class="header">
  <div class="brand"><span class="brand-mark"></span><span class="brand-name">Pellworth &amp; Quine</span></div>
  <div class="cert-badge" role="img" aria-label="SDVOSB certification badge"></div>
</header>

<nav class="nav">
  <a href="#home" style="left:70px">HOME</a>
  <a href="#about" style="left:158px">ABOUT US</a>
  <a href="#services" style="left:270px">SERVICES</a>
  <a href="#why" style="left:380px">WHY HIRE US?</a>
  <a href="#blog" style="left:520px">BLOG</a>
  <a href="#partners" style="left:600px">PARTNERS</a>
  <a href="#contact" style="left:713px">CONTACT US</a>
  <div class="nav-phone">
    <svg width="20" height="20" viewBox="0 0 24 24"><path fill="#fff" d="M6.6 10.8a15.1 15.1 0 0 0 6.6 6.6l2.2-2.2c.3-.3.7-.4 1-.2 1.1.4 2.3.6 3.6.6.6 0 1 .4 1 1V20c0 .6-.4 1-1 1A17 17 0 0 1 3 4c0-.6.4-1 1-1h3.5c.6 0 1 .4 1 1 0 1.3.2 2.5.6 3.6.1.3 0 .7-.2 1z"/></svg>
    <span>202-555-0148</span>
  </div>
</nav>

<section class="hero" id="home" role="img" aria-label="Photo of a consultant reviewing strategic planning charts at a desk">
  <div class="hero-caption" style="top:146px;left:104px">
    <h1 style="left:0;padding-left:0;position:absolute;left:0"><span style="position:relative;left:0">&nbsp;</span></h1>
  </div>
</section>
<div class="abs" style="left:104px;top:368px;width:527px;height:160px;background:rgba(20,24,28,.9)"></div>
<h1 class="abs" style="left:104px;top:382px;font-size:41px;font-weight:700;color:#fff;letter-spacing:.5px">STRATEGIC PLANNING</h1>
<p class="abs" style="left:104px;top:438px;width:510px;font-size:20px;line-height:27px;color:#fff">Lanventore veritatis et quasi architecto beatae vitae dicta sunt explicabo..</p>
<a class="btn" style="left:104px;top:511px;width:179px;height:50px">Read More</a>
<div class="hero-dots" style="top:620px"><span class="active"></span><span></span><span></span><span></span></div>

<section id="about">
  <h2 class="section-title" style="top:786px">COMPANY OVERVIEW</h2>
  <p class="overview-text">Pellworth &amp; Quine, LLC is a minority owned Service Disabled Veteran Owned Small Business (SDVOSB) that provides Strategic Planning, Public Health Emergency Response, and Data Management Solutions for Federal Civilian and Defense Agencies. We have over 20 years of experience helping health and defense agencies develop concept of operations, deploy assets and personnel in Hot Zones around the world, and deliver goods and services all of the globe.</p>
  <a class="btn" style="left:511px;top:979px;width:178px;height:48px">Read More</a>
</section>

<section class="services" id="services">
  <h2 class="section-title">OUR SERVICES</h2>

  <div class="service-card" style="left:76px;top:149px">
    <svg style="top:34px" width="70" height="78" viewBox="0 0 70 78" fill="none" stroke="#2c4a5d" stroke-width="3"><path d="M4 3h40l22 22v50H4z"/><path d="M44 3v22h22"/><path d="M14 40h42M14 50h42M14 60h42"/></svg>
    <h3 style="top:138px">Strategic Planning</h3>
    <ul style="top:166px"><li>Organizational Needs Assessment</li><li>Roadmap Development</li><li>Marketing Outreach</li><li>Cost Benefit and Alternative Analysis</li></ul>
  </div>
  <a class="btn" style="left:150px;top:479px;width:180px;height:50px">Read More</a>

  <div class="service-card" style="left:437px;top:113px;height:350px">
    <svg style="top:24px" width="80" height="66" viewBox="0 0 80 66" fill="none" stroke="#2c4a5d" stroke-width="3"><rect x="3" y="14" width="74" height="49" rx="3"/><path d="M28 14V4h24v10"/><path d="M35 28h10v9h9v10h-9v9H35v-9h-9V37h9z"/></svg>
    <h3 style="top:112px">Public Health Emergency Response</h3>
    <ul style="top:162px"><li>Crisis Management</li><li>Disaster Relief Planning</li><li>Asset and Personnel Deployment</li><li>Financial Impact Analysis</li></ul>
  </div>
  <a class="btn" style="left:511px;top:444px;width:180px;height:50px">Read More</a>

  <div class="service-card" style="left:797px;top:149px">
    <svg style="top:34px" width="72" height="78" viewBox="0 0 72 78" fill="none" stroke="#2c4a5d" stroke-width="3"><ellipse cx="36" cy="10" rx="32" ry="8"/><path d="M4 10v58c0 4.4 14.3 8 32 8s32-3.6 32-8V10"/><path d="M4 25c0 4.4 14.3 8 32 8s32-3.6 32-8M4 40c0 4.4 14.3 8 32 8s32-3.6 32-8M4 55c0 4.4 14.3 8 32 8s32-3.6 32-8"/></svg>
    <h3 style="top:138px">Data Management Services</h3>
    <ul style="top:166px"><li>Cloud Migration Strategy</li><li>Disaster Recovery Strategy</li><li>Records Management</li><li>Data Analytics</li></ul>
  </div>
  <a class="btn" style="left:872px;top:479px;width:180px;height:50px">Read More</a>
</section>

<section id="leadership">
  <h2 class="section-title" style="top:1698px">LEADERSHIP TEAM</h2>

  <div class="photo" style="left:76px;top:1766px;width:528px;height:371px;background:linear-gradient(100deg,#8a8f8c 0%,#c9ccc8 40%,#e6e7e3 70%,#d2d6d2 100%)" role="img" aria-label="Portrait photo of the chief executive officer"></div>
  <div class="name-tag" style="left:408px;top:1796px;width:244px;height:116px">
    <h4>Ret. SFC Marcus D.<br>Pellworth</h4>
    <span>Chief Executive Office</span>
  </div>
  <p class="bio" style="left:689px;top:1812px;width:432px">Pellworth &amp; Quine, LLC was founded by Retired Sergeant First Class (Ret. SFC) Marcus Pellworth. Mr. Pellworth retired from the US Army after over 20 years of service which included tours in "Operation Desert Storm/Shield" , two tours of duty at the DMZ in Korea, also served in various locations in Germany including the Berlin Wall, and a Tour in Bosnia, Herzegovina for operation "Deliberate Force".</p>
  <a class="btn" style="left:689px;top:2024px;width:179px;height:49px">Read More</a>

  <div class="photo" style="left:617px;top:2140px;width:509px;height:370px;background:linear-gradient(100deg,#b9c6cc 0%,#dde3e5 35%,#7c8a91 60%,#3a3f45 100%)" role="img" aria-label="Portrait photo of the business development manager"></div>
  <div class="name-tag" style="left:548px;top:2165px;width:247px;height:120px">
    <h4>Mr. Daniel T.<br>Quine</h4>
    <span>Business Development<br>Manager</span>
  </div>
  <p class="bio" style="left:76px;top:2201px;width:450px">Mr. Quine brings over 10 years of business development experience to Pellworth &amp; Quine LLC. Prior to joining, Mr. Quine led business development capture for large and midsize defense companies in the Washington DC area servicing agencies such as the Army, US Air Force, the Defense Logistics Agency, Center for Disease Control, Food and Drug Administration and the Federal Aviation Administration (FAA).</p>
  <a class="btn" style="left:76px;top:2411px;width:178px;height:49px">Read More</a>
</section>

<section class="why" id="why">
  <h2>WHY HIRE US?</h2>
  <ul>
    <li><svg width="16" height="16" viewBox="0 0 16 16"><circle cx="8" cy="8" r="8" fill="#f7941d"/><path d="M4.5 8.2l2.3 2.3 4.7-4.8" stroke="#fff" stroke-width="1.8" fill="none"/></svg>Over 20 years of experience deploying assets and personnel to disaster zones around the US and the world.</li>
    <li><svg width="16" height="16" viewBox="0 0 16 16"><circle cx="8" cy="8" r="8" fill="#f7941d"/><path d="M4.5 8.2l2.3 2.3 4.7-4.8" stroke="#fff" stroke-width="1.8" fill="none"/></svg>Over 20 years of experience developing concept of operations and stakeholder management strategies for Federal Agencies.</li>
    <li><svg width="16" height="16" viewBox="0 0 16 16"><circle cx="8" cy="8" r="8" fill="#f7941d"/><path d="M4.5 8.2l2.3 2.3 4.7-4.8" stroke="#fff" stroke-width="1.8" fill="none"/></svg>Over 10 years of experience with database management and replications</li>
    <li><svg width="16" height="16" viewBox="0 0 16 16"><circle cx="8" cy="8" r="8" fill="#f7941d"/><path d="M4.5 8.2l2.3 2.3 4.7-4.8" stroke="#fff" stroke-width="1.8" fill="none"/></svg>Highly educated consultants with over 90% possessing advance degrees and industry certifications.</li>
  </ul>
</section>
<div class="why-brand">
  <div class="brand"><span class="brand-mark"></span><span class="brand-name">Pellworth &amp; Quine</span></div>
</div>

<section id="partners">
  <h2 class="section-title" style="top:2976px">OUR PARTNERS</h2>
  <div class="partner boxed" style="left:76px">Brightmoor</div>
  <div class="partner" style="left:345px">Calder Ashby</div>
  <div class="partner" style="left:615px">Northvale Systems</div>
  <div class="partner" style="left:884px">Meridian Dynamics</div>
</section>

<footer class="footer" id="contact">
  <div class="brand"><span class="brand-mark"></span><span class="brand-name">Pellworth &amp; Quine</span></div>
  <p class="footer-copy">Copyright © 2018. Company Name.<br>All Right Reserved</p>
  <div class="socials"><span></span><span></span><span></span><span></span></div>

  <h5 style="left:343px">SITE MAP</h5>
  <div class="rule" style="left:343px;width:240px"></div>
  <ul style="left:343px"><li>Home</li><li>About Us</li><li>Services</li><li>Why Hire Us?</li></ul>
  <ul style="left:474px"><li>Blog</li><li>Partners</li><li>Contact Us</li></ul>

  <h5 style="left:617px">OUR CAPABILITIES</h5>
  <div class="rule" style="left:617px;width:240px"></div>
  <ul style="left:617px"><li>Strategic Planning</li><li>Public Health Emergency Response</li><li>Data Management Services</li><li>Contracts Vehicles</li></ul>

  <h5 style="left:884px">CONTACT INFO</h5>
  <div class="rule" style="left:884px;width:246px"></div>
  <ul style="left:884px;top:92px">
    <li style="line-height:20px">1870 Linden Ridge Dr<br>Atlanta, GA</li>
    <li style="margin-top:6px"><svg width="12" height="12" viewBox="0 0 24 24"><path fill="#cfcfcf" d="M6.6 10.8a15.1 15.1 0 0 0 6.6 6.6l2.2-2.2c.3-.3.7-.4 1-.2 1.1.4 2.3.6 3.6.6.6 0 1 .4 1 1V20c0 .6-.4 1-1 1A17 17 0 0 1 3 4c0-.6.4-1 1-1h3.5c.6 0 1 .4 1 1 0 1.3.2 2.5.6 3.6.1.3 0 .7-.2 1z"/></svg>202-555-0148</li>
    <li><svg width="12" height="10" viewBox="0 0 24 18"><rect width="24" height="18" fill="#cfcfcf"/><path d="M0 0l12 9 12-9" stroke="#232323" stroke-width="2" fill="none"/></svg>info@pellworthquine.com</li>
  </ul>
</footer>

</body>
</html>
```